Local Flower Farm Needs Business Card Design

I need business cards designed for a flower farm based in Eudora, Kansas.
Business Info:
We are a local cut flower farm located in Eudora, Kansas, founded by Corinne Haldwick. What started as a passion for agriculture and search for more joy in daily life has blossomed into a small business dedicated to providing the community with beautiful, fresh, and sustainable flowers. We specialize in local, seasonal blooms, ensuring that every petal reflects the care and dedication we pour into our craft. Our mission is to deliver the highest quality flowers directly to our customers through local farmers markets and to florists who share our commitment to sustainability. Join us in celebrating the beauty of nature, one bloom at a time!
Contact Details:
Corinne Haldwick
Owner
Phone 913-555-0147
Facebook: Rosalind Thorpe Gardens
Instagram: @RosalindThorpeGardens
Website: RosalindThorpeGardens.example
Target Market(s)
Wholesale to Florists and Direct to Consumer via Farmers Market
Industry/Entity Type
Florist, Farm
Contact Information for Business Card
Name, Contact Info, Logo
Look and feel
Each slider illustrates characteristics of the customer's brand and the style your logo design should communicate.

```html
<!DOCTYPE html>
<html lang="en">
<head>
<meta charset="utf-8">
<title>Rosalind Thorpe Gardens – Business Card</title>
<link href="https://fonts.googleapis.com/css2?family=Arimo:wght@400;700&display=swap" rel="stylesheet">
<style>
  :root {
    --backdrop: #2b2d30;
    --teal-deep: #0d3437;
    --teal-mid: #1f5b5d;
    --paper: #ffffff;
    --ink: #0d3437;
    --muted: #4a5a5c;
  }
  * { margin: 0; padding: 0; box-sizing: border-box; }
  html, body {
    width: 1200px; height: 900px; overflow: hidden;
    background: var(--backdrop);
    font-family: "Arimo", Arial, sans-serif;
  }
  .sheet {
    width: 1200px; height: 900px;
    display: flex; align-items: center; justify-content: center; gap: 60px;
  }
  .card {
    position: relative;
    width: 525px; height: 300px;
    border-radius: 22px;
    overflow: hidden;
    box-shadow: 0 10px 30px rgba(0,0,0,.45);
  }
  .card--front { background: var(--paper); }
  .card--back { background: var(--teal-deep); display: flex; align-items: center; justify-content: center; }
  .card__wave { position: absolute; inset: 0; width: 100%; height: 100%; }

  .brand-mark {
    position: absolute;
    display: flex; align-items: center; justify-content: center;
    border-radius: 50%;
    text-align: center;
    font-family: "Arimo", Arial, sans-serif;
    font-weight: 400;
    text-transform: uppercase;
    letter-spacing: 1.5px;
    line-height: 1.35;
  }
  .card--front .brand-mark {
    left: 34px; top: 22px; width: 122px; height: 122px;
    border: 1.5px solid var(--ink); color: var(--ink); font-size: 11.5px;
  }
  .card--back .brand-mark {
    position: static; width: 150px; height: 150px;
    border: 1.5px solid var(--paper); color: var(--paper); font-size: 14px;
  }

  .identity { position: absolute; right: 34px; top: 92px; text-align: right; }
  .identity__name { font-weight: 700; font-size: 20px; color: var(--ink); letter-spacing: .5px; text-transform: uppercase; }
  .identity__role { font-size: 12px; color: var(--muted); margin-top: 3px; }

  .contact { position: absolute; right: 30px; top: 190px; list-style: none; text-align: right; }
  .contact__item {
    display: flex; align-items: center; justify-content: flex-end; gap: 7px;
    color: var(--paper); font-size: 13px; line-height: 21px;
  }
  .contact__icon { width: 11px; height: 11px; flex: none; }
</style>
</head>
<body>
<main class="sheet">
  <section class="card card--front" aria-label="Business card front">
    <svg class="card__wave" viewBox="0 0 525 300" preserveAspectRatio="none" aria-hidden="true">
      <path d="M0,70 C30,150 140,178 270,168 S460,145 525,150 L525,300 L0,300 Z" fill="var(--teal-mid)"/>
      <path d="M0,84 C34,160 140,186 270,176 S460,153 525,158 L525,300 L0,300 Z" fill="var(--paper)"/>
      <path d="M0,96 C38,172 140,196 270,186 S460,162 525,166 L525,300 L0,300 Z" fill="var(--teal-deep)"/>
    </svg>

    <div class="brand-mark">Rosalind<br>Thorpe<br>Gardens</div>

    <div class="identity">
      <p class="identity__name">Corinne Haldwick</p>
      <p class="identity__role">Owner</p>
    </div>

    <ul class="contact">
      <li class="contact__item">913-555-0147
        <svg class="contact__icon" viewBox="0 0 12 12"><path d="M2.5 1 L4.5 1 L5.2 3.6 L4 4.6 C4.6 6 5.9 7.4 7.4 8 L8.4 6.8 L11 7.5 L11 9.5 C11 10.3 10.3 11 9.5 11 C5 11 1 7 1 2.5 C1 1.7 1.7 1 2.5 1 Z" fill="var(--paper)"/></svg>
      </li>
      <li class="contact__item">Rosalind Thorpe Gardens
        <svg class="contact__icon" viewBox="0 0 12 12"><circle cx="6" cy="6" r="5" fill="var(--paper)"/></svg>
      </li>
      <li class="contact__item">@RosalindThorpeGardens
        <svg class="contact__icon" viewBox="0 0 12 12"><circle cx="6" cy="6" r="4.6" fill="none" stroke="var(--paper)" stroke-width="1.4"/></svg>
      </li>
      <li class="contact__item">RosalindThorpeGardens.example
        <svg class="contact__icon" viewBox="0 0 12 12"><circle cx="6" cy="6" r="5" fill="none" stroke="var(--paper)" stroke-width="1.1"/><path d="M1 6 H11 M6 1 C3.5 3.5 3.5 8.5 6 11 M6 1 C8.5 3.5 8.5 8.5 6 11" fill="none" stroke="var(--paper)" stroke-width="0.9"/></svg>
      </li>
    </ul>
  </section>

  <section class="card card--back" aria-label="Business card back">
    <div class="brand-mark">Rosalind<br>Thorpe<br>Gardens</div>
  </section>
</main>
</body>
</html>
```